PostCard Design Project

I am making a mailing postcard
I am having the mailing printed using 4 color foil on certain parts.
I am looking for a design that maximizes the foil process where certain parts are done in foil to grab the customers attention (example: if there is a car on the postcard the headlights would be done in foil) .
I am targeting some industries, (auto, real estate, medical, beauty) I would like the post card to have examples of postcard ideas for 2 or 3 of these industries.
specs:
the postcard should be atleast 6.5x9 up to 8.5x11, I don't want to restrict the space for the creative as I don't want everything to look like a huge mess. both sides will be used.
the piece is a direct mail piece so it has to meet requirements of https://www.mailvantor.com/business/pdf/quick-reference-guide.pdf
text will be
"business with no limits, meet mailing with no addresses, gain new customers through "Open Porch Route Drop" reach new customers at their home without needing their address. "
I also want some current print specials I am running included.
-double your order FREE (order 500 business cards and get 1000)
-250 100lb gloss stock brochures 99.00
-business packages (cards, envelopes and letterhead) 299
-1000 flyers 140.40
-5000 postcards 179.99
A list of services
banners
booklets
brochures
business cards
calendars
catalogs
CD/DVD packages
envelopes
event tickets
flyers
hangtags
postcards
posters
presentation folders
rack cards
labels
table tents
window cling and decal
"order 24/7 orders@inkwillow.com" must be included
my logo is InkWillow will be supplied later
ive received some great designs. however Im looking for something a little more modern like some zorvel would put out. if the amount of words is too much please feel free to edit. also an idea i had for the list of services i offer is to have it transparent yet readable as the background of the postcard some small some big but covering the entire backgroud. you can then design on top of that with other thing. just an early morning thought
Reason: I have uploaded a sketch of my idea, please take time to look at it for an accurate depiction of what im looking for. feel free to add elements that make it pop off the page
Reason: We are getting close i will be providing feed back today

```html
<!DOCTYPE html>
<html lang="en">
<head>
<meta charset="utf-8">
<title>InkWillow Postcard</title>
<link rel="stylesheet" href="https://fonts.googleapis.com/css2?family=Open+Sans:wght@600;700&display=swap">
<style>
  :root {
    --page: #e9e9ea;
    --card: #0b0b0b;
    --card-glow: #2a2a2a;
    --ink: #ffffff;
    --stamp: #ffffff;
    --stamp-ink: #111111;
    --mosaic: linear-gradient(90deg, #e63946, #f4a261, #f6e05e, #6ac46a, #2a9d8f, #48b5e8, #3a5ba9, #8e44ad, #e76fb0, #8b5a2b, #f0e6d2, #e63946, #f4a261, #6ac46a, #48b5e8, #8e44ad);
  }
  * { box-sizing: border-box; margin: 0; padding: 0; }
  html, body {
    width: 1200px; height: 900px; overflow: hidden;
    background: var(--page);
    font-family: "Open Sans", Arial, sans-serif;
    color: var(--ink);
  }
  .postcard {
    position: absolute; left: 220px; width: 760px; height: 400px;
    background: radial-gradient(ellipse at 55% 40%, var(--card-glow), var(--card) 65%);
    overflow: hidden;
  }
  .postcard--front { top: 35px; }
  .postcard--back { top: 465px; }
  .mosaic-band {
    position: absolute; left: 0; right: 0; height: 28px;
    background: var(--mosaic);
    opacity: .9;
  }
  .mosaic-band--top { top: 0; }
  .mosaic-band--bottom { bottom: 0; }

  .headline {
    position: absolute; top: 42px; left: 30px; right: 30px;
    text-align: center; font-weight: 700; font-size: 19px; line-height: 1.35;
  }
  .sample-collage {
    position: absolute; left: 60px; top: 140px; width: 300px; height: 200px;
    background: linear-gradient(135deg, #3aa0dd, #f2f2f2 45%, #f4c430 80%, #e05a7a);
    border-radius: 4px;
  }
  .sample-fan {
    position: absolute; right: 70px; top: 130px; width: 150px; height: 80px;
    background: linear-gradient(120deg, #2bb3c0, #f4f4f4 50%, #e04b6b);
    border-radius: 4px;
  }
  .specials {
    position: absolute; left: 390px; top: 220px; list-style: none;
    font-weight: 700; font-size: 13px; line-height: 1.4;
  }
  .tick-list li::before { content: "\2713"; margin-right: 7px; }
  .specials .note { padding-left: 17px; }
  .specials .note::before { content: none; }
  .order-line {
    position: absolute; left: 30px; bottom: 40px;
    font-weight: 600; font-size: 18px;
  }

  .postage-stamp {
    position: absolute; right: 40px; top: 45px; width: 76px; height: 48px;
    background: var(--stamp); color: var(--stamp-ink);
    font-size: 10px; font-weight: 600; line-height: 1.2;
    display: flex; align-items: center; justify-content: center; text-align: center;
  }
  .services-title {
    position: absolute; top: 125px; left: 0; right: 0; text-align: center;
    font-weight: 700; font-size: 21px;
  }
  .services {
    position: absolute; top: 180px; list-style: none;
    font-weight: 600; font-size: 17px; line-height: 1.55;
  }
  .services--a { left: 90px; }
  .services--b { left: 320px; }
  .services--c { left: 530px; }
</style>
</head>
<body>
  <section class="postcard postcard--front">
    <div class="mosaic-band mosaic-band--top" role="img" aria-label="Border of multicoloured square tiles"></div>
    <h1 class="headline">“ Business with no limits, meet mailing with no addresses,<br>Gain new customers through ‘Open Porch Route Drop’<br>Reach new customers at their home without needing their address. ”</h1>
    <div class="sample-collage" role="img" aria-label="Fanned stack of printed flyers and brochures"></div>
    <div class="sample-fan" role="img" aria-label="Fan of printed business cards"></div>
    <ul class="specials tick-list">
      <li>Double your order FREE</li>
      <li class="note">(order 500 business cards and get 1000)</li>
      <li>250 100lb gloss stock brochures 99.00</li>
      <li>Business packages</li>
      <li class="note">(cards, envelopes and letterhead) 299</li>
      <li>1000 flyers 140.40</li>
      <li>5000 postcards 179.99</li>
    </ul>
    <p class="order-line">order 24/7 orders@inkwillow.com</p>
    <div class="mosaic-band mosaic-band--bottom" role="img" aria-label="Border of multicoloured square tiles"></div>
  </section>

  <section class="postcard postcard--back">
    <div class="mosaic-band mosaic-band--top" role="img" aria-label="Border of multicoloured square tiles"></div>
    <div class="postage-stamp">Postage<br>Stamp</div>
    <h2 class="services-title">Our Services Are</h2>
    <ul class="services services--a tick-list">
      <li>banners</li><li>booklets</li><li>brochures</li>
      <li>business cards</li><li>calendars</li><li>catalogs</li>
    </ul>
    <ul class="services services--b tick-list">
      <li>CD/DVD packages</li><li>envelopes</li><li>event tickets</li>
      <li>flyers</li><li>hangtags</li><li>postcards</li>
    </ul>
    <ul class="services services--c tick-list">
      <li>posters</li><li>presentation folders</li><li>rack cards</li>
      <li>labels</li><li>table tents</li><li>window cling and decal</li>
    </ul>
    <div class="mosaic-band mosaic-band--bottom" role="img" aria-label="Border of multicoloured square tiles"></div>
  </section>
</body>
</html>
```